BUN AND BITE WALL POSTER

Hi designer,

I would like to create a poster to put on my wall.

My intention is to place a bicycle onto a wall and have these words vinyl stick next to it.

" Life is not a race.
It is a journey
Enjoy each moment. Relax!
Have a bowl of Bun and Bite
Make all your dreams come true "

I like traditional fonts - easy to read. See example. This is something I would love.

It will be on a white wall so black text would be ok. I have also attached my logo - maybe try include Bun and Bite font in your design if possible - but not important.

Good luck everyone.

Font styles to use
Decorative
Script

Requirements
Must have
• The placement of my bike will be on the top left corner of the wall so I think it will be best fit if all designs are done in horizontal rectangular shape (landscape)

```html
<!DOCTYPE html>
<html lang="en">
<head>
<meta charset="utf-8">
<title>Bun and Bite Wall Poster</title>
<link rel="stylesheet" href="https://fonts.googleapis.com/css2?family=Damion&display=swap">
<style>
  :root {
    --wall: #ffffff;
    --ink: #111111;
  }
  html, body {
    margin: 0;
    padding: 0;
    width: 1200px;
    height: 1000px;
    overflow: hidden;
    background: var(--wall);
  }
  .poster {
    position: relative;
    width: 1200px;
    height: 1000px;
    background: var(--wall);
    overflow: hidden;
  }
  .quote {
    position: absolute;
    left: 568px;
    top: 0;
    margin: 0;
    color: var(--ink);
  }
  .quote-line {
    position: absolute;
    left: 0;
    white-space: nowrap;
    line-height: 1;
    font-family: "Damion", "Brush Script MT", cursive;
    font-weight: 400;
    font-size: 54px;
    transform: skewX(-6deg);
    transform-origin: left bottom;
  }
  .quote-line--accent {
    font-family: "Damion", "Brush Script MT", cursive;
    font-weight: 700;
    letter-spacing: -1px;
  }
  .line-race    { top: 92px;  left: 20px; }
  .line-journey { top: 172px; }
  .line-moment  { top: 252px; }
  .line-relax   { top: 336px; left: 8px; font-size: 92px; }
  .line-bowl    { top: 466px; left: 2px; }
  .line-brand   { top: 540px; left: 8px; font-size: 100px; }
  .line-make    { top: 660px; left: 4px; }
  .line-dreams  { top: 744px; left: 4px; }
</style>
</head>
<body>
  <main class="poster">
    <p class="quote">
      <span class="quote-line line-race">Life is not a race.</span>
      <span class="quote-line line-journey">It is a journey</span>
      <span class="quote-line line-moment">Enjoy each moment.</span>
      <span class="quote-line quote-line--accent line-relax">Relax !</span>
      <span class="quote-line line-bowl">Have a bowl of</span>
      <span class="quote-line quote-line--accent line-brand">Bun and Bite</span>
      <span class="quote-line line-make">Make all your</span>
      <span class="quote-line line-dreams">dreams come true</span>
    </p>
  </main>
</body>
</html>
```